Refinery Service Website (Wholesale) – Luxurious Landing Pages & Industry Hub

We are seeking talented designers to create a luxurious and professional redesign for the wholesale section of our refinery service website, Steadfast KLV. Our current refinery page (https://steadfastklv.com/refinery/) and dental landing page (https://steadfastklv.com/refinery/dental-gold/) provide functional starting points with existing content (words, sections, trust badges, and video placeholders) that must be retained and enhanced with a sophisticated, high-end aesthetic. We serve high-net-worth wholesale clients across industries such as dental practices, mortuaries, estate attorneys, dentists, pawnshops, jewelry stores, and financial advisors. The project includes designing a revamped main wholesale landing page, individual landing pages for each industry with specific sections, and a central hub page to showcase these industries in an SEO-friendly and user-focused way, all while elevating the design to a luxurious standard.

Project Overview
Our refinery service specializes in precious metals and serves a variety of industries through wholesale access. We want the wholesale section of our website to exude sophistication and exclusivity while preserving and enhancing the existing content on our pages. Currently:
• Our refinery page (https://steadfastklv.com/refinery/) provides a basic overview of our services with text, sections, and trust badges, but it lacks visual appeal and a high-end feel.
• Our dental landing page (https://steadfastklv.com/refinery/dental-gold/) targets dental professionals with relevant messaging, sections, and content, but it also feels utilitarian and could benefit from a more elegant design, improved layout, and stronger calls-to-action.
Designers must use the existing words, sections, trust badges, and video placeholders from these pages as a foundation, enhancing them with a luxurious redesign and adding the additional sections specified below. We admire the clean and professional look of https://www.brovelmetalworks.com/, but we aim to elevate our design with a more luxurious and exclusive feel to attract discerning wholesale clients. The redesign will involve:
1 Main Wholesale Landing Page: A complete overhaul of our current refinery page into a luxurious and professional entry point, retaining and enhancing existing content while improving the overall design.
2 Industry-Specific Landing Pages: A dedicated landing page for each of the following industries: dental practices, mortuaries, estate attorneys, dentists, pawnshops, jewelry stores, and financial advisors. Each page must retain and enhance existing content (where applicable) and include specific sections (detailed below) to build trust, provide information, and encourage engagement.
3 Industry Hub Page: A central page that showcases all the industries we serve in a visually appealing and SEO-optimized manner, acting as a gateway to each industry-specific landing page.
Our website is built on WordPress using the Tiles Composer, so design submissions should be provided in HTML, CSS, or as a Figma file for seamless integration. The design must be responsive, visually striking, and optimized for usability across all devices (desktop, tablet, mobile).
Project Scope
We are looking for design submissions that include:
• Main Wholesale Landing Page: A redesigned version of our current refinery page (https://steadfastklv.com/refinery/), transformed into a luxurious and professional entry point for our wholesale services. The new design must retain the existing words, sections, trust badges, and any video placeholders, enhancing them with a high-end aesthetic while improving layout and engagement.
• Industry-Specific Landing Pages: A dedicated landing page for each of the following industries: dental practices, mortuaries, estate attorneys, dentists, pawnshops, jewelry stores, and financial advisors. Each page must:
◦ Retain and enhance existing content (words, sections, trust badges, video placeholders) from pages like our dental landing page (https://steadfastklv.com/refinery/dental-gold/) as a reference, adapting it for each industry. For industries without existing pages, mirror the structure and content style of the dental page while tailoring the messaging and visuals.
◦ Include the following additional sections to enhance functionality and trust:
Trust Badges: A section displaying trust signals (e.g., certifications, accreditations, years in business) to build credibility with visitors. Include placeholders for 4–6 badges/icons, enhancing any existing badges from our current pages.
Testimonials: A section featuring 3–5 customer testimonials with placeholders for quotes, names, and industries (e.g., “Dr. Colm Varga, Dental Practice Owner”). If testimonials exist on current pages, enhance their presentation.
Contact Information: A clearly visible section with contact details (e.g., phone number, email, address) styled to match the luxurious aesthetic, improving any existing contact info presentation.
Contact Fillout Form: A user-friendly form for inquiries, including fields for name, email, industry, and message, with a professional design that encourages submissions, enhancing any existing forms.
Shipping Information: A section detailing shipping instructions and processes (e.g., how to send materials for refining), presented clearly and concisely, building on any existing shipping details.
Summary Service Bullet Points: A concise list of 5–7 key services or benefits tailored to the specific industry (e.g., “Fast turnaround for dental scrap” for dental pages, “Secure handling for jewelry inventory” for jewelers), improving any existing bullet points.
Video: Shipping Instructions: A placeholder for a video explaining how to ship materials to us, styled with a play button and a luxurious frame, enhancing any existing video placeholders.
Video: How Our Refinery Works: A placeholder for a video detailing our refining process, designed to match the aesthetic of the page, enhancing any existing video placeholders.
Video: Who We Are: A placeholder for a video introducing our company and values, presented in an elegant and professional manner, enhancing any existing video placeholders.
◦ Include tailored messaging and design elements that resonate with the specific industry (e.g., dental tools and scrap refining benefits for dental pages, elegant estate visuals for attorneys, jewelry displays for jewelers).
◦ Maintain a cohesive design that ties back to the overall luxurious aesthetic of the wholesale section.
• Industry Hub Page: A central hub page that showcases all the industries we serve in an SEO-friendly and visually engaging way. This page should include:
◦ A grid, carousel, or categorized layout featuring each industry with a concise description or tagline (e.g., “Dental Practices: Turn Scrap into Profit”).
◦ Links to each industry-specific landing page for easy navigation.
◦ Design elements that encourage exploration (e.g., hover effects, icons, or visuals representing each industry).
◦ SEO optimization through keyword-rich headings, meta-friendly layouts, and content areas that naturally incorporate industry terms.
• SEO and User Engagement Focus: The design should balance aesthetics with functionality, ensuring that both the hub page and individual landing pages are optimized for search engines (e.g., through clear headings, meta-friendly layouts) and capture user attention with compelling calls-to-action (e.g., “Discover Refinery Solutions for Your Dental Practice” or “Maximize Value for Your Jewelry Inventory”).
Design Requirements
• Aesthetic: Luxurious, elegant, and professional, with a focus on high-net-worth wholesale clients. The current designs (https://steadfastklv.com/refinery/ and https://steadfastklv.com/refinery/dental-gold/) are too basic and functional; we want a high-end look that conveys prestige and trust, using elements like deep golds, silvers, blacks, or whites to evoke luxury while enhancing existing content.
• Typography: Clean, modern, and sophisticated fonts that enhance readability and align with a high-end brand image, improving upon existing typography.
• Imagery: Incorporate placeholders for high-quality imagery relevant to each industry (e.g., dental tools, jewelry displays, legal documents). No stock images required in submissions—just placeholders. Retain and enhance any existing imagery placeholders from our current pages.
• Video Placeholders: Video sections (for shipping instructions, how the refinery works, and who we are) should include placeholders with play buttons and elegant frames that match the luxurious aesthetic, enhancing any existing video placeholders on our current pages.
• Responsiveness: The design must be fully responsive and look great on desktop, tablet, and mobile devices.
• SEO Optimization: The layout should support SEO best practices, such as clear heading structures (H1, H2, etc.), alt-text-friendly image placeholders, and keyword-rich content areas for each industry, building on existing content for SEO purposes.
• Deliverables Format: Submissions should include design files in HTML, CSS, or Figma format, ready for integration into WordPress with Tiles Composer.

Submission Guidelines
We invite designers to submit their concepts based on the following:
• A mockup of the redesigned main wholesale landing page, improving upon our current refinery page (https://steadfastklv.com/refinery/), retaining and enhancing existing words, sections, trust badges, and video placeholders with a luxurious aesthetic.
• A mockup of the industry hub page showcasing all the industries we serve (dental practices, mortuaries, estate attorneys, dentists, pawnshops, jewelry stores, financial advisors).
• At least two examples of industry-specific landing pages (e.g., one for dental practices, improving upon our current dental page (https://steadfastklv.com/refinery/dental-gold/), and one for jewelry stores), showing how the design retains and enhances existing content, incorporates all required sections (trust badges, testimonials, contact info, contact form, shipping info, service bullet points, and video placeholders), and tailors messaging to each audience.
• A brief explanation of your design choices, including how they enhance SEO, tailor messaging for each industry, incorporate and enhance existing content, include the required sections, and align with the luxurious and professional aesthetic we’re seeking.
• Files in HTML, CSS, or Figma format to demonstrate how the design can be implemented.

Judging Criteria
Submissions will be evaluated based on:
• Alignment with the luxurious and professional aesthetic described, significantly improving upon our current designs (https://steadfastklv.com/refinery/ and https://steadfastklv.com/refinery/dental-gold/) while retaining and enhancing existing content.
• Effective retention and enhancement of existing words, sections, trust badges, and video placeholders from our current pages, seamlessly integrating them into the new design.
• Inclusion and effective design of all required sections (trust badges, testimonials, contact info, contact form, shipping info, service bullet points, and video placeholders) on the industry-specific landing pages.
• Creativity and effectiveness in tailoring messaging and visuals for each industry-specific landing page.
• Usability and visual appeal of the industry hub page, including its potential to improve SEO and engage users.
• Suitability for the target audience (high-net-worth wholesale clients in dental, mortuary, legal, pawnshop, jewelry, and financial sectors).
• Compatibility with WordPress and Tiles Composer (based on the format of deliverables).

Additional Notes
• We are open to creative interpretations of “luxury” and encourage designers to think outside the box while maintaining professionalism. Use our current pages as a foundation for content and structure, enhancing and building upon them rather than replacing them entirely.
• The industry hub page should feel intuitive and encourage exploration, potentially using layouts like a grid, carousel, or categorized sections with hover effects.
• Each industry-specific landing page should include a unique value proposition (e.g., “Streamline Your Dental Scrap Refining Process” or “Maximize Value for Your Jewelry Inventory”) to capture attention, building on the clarity of our current dental page but with a more luxurious presentation and all required sections.
• We will provide feedback during the contest and may request revisions from top submissions.

About Us
Steadfast KLV is a leading refinery service provider specializing in precious metals, offering wholesale solutions to a wide range of industries such as dental, jewelry, and legal sectors. Our goal is to create a luxurious online presence that reflects the high value we provide to our clients.
We look forward to seeing your creative designs and how you can bring our vision of a luxurious, industry-focused wholesale section to life!

```html
<!DOCTYPE html>
<html lang="en">
<head>
<meta charset="utf-8">
<title>Steadfast KLV – Precious Metal Refinery</title>
<link href="https://fonts.googleapis.com/css2?family=Montserrat:wght@400;500;600;700;800;900&display=swap" rel="stylesheet">
<style>
:root{
  --ink:#141414;
  --ink-soft:#2a2a2a;
  --gold:#c8924c;
  --gold-dark:#b5843f;
  --gold-band:#ba8a4c;
  --gold-panel:#c99a5b;
  --beige:#f4e7d4;
  --grey-bg:#efefef;
  --text:#333;
  --muted:#666;
  --white:#fff;
  --up:#c8924c;
}
*{box-sizing:border-box;margin:0;padding:0}
html,body{width:1200px;height:5391px;overflow:hidden}
body{font-family:"Montserrat",Arial,sans-serif;color:var(--text);background:var(--white);position:relative}
section,header,footer{position:absolute;left:0;width:1200px}
.btn{display:inline-block;background:var(--gold);color:#fff;font-size:10px;font-weight:700;letter-spacing:.5px;text-transform:uppercase;padding:0 20px;height:32px;line-height:32px;border-radius:2px}

/* hero */
.hero{top:0;height:716px;background:#0c0906;overflow:hidden}
.hero-photo{position:absolute;inset:0;background:radial-gradient(ellipse 360px 420px at 560px 520px,#ffb13a 0%,#e86a12 30%,#6a2a08 62%,#120a06 85%),#0c0906}
.ticker{position:absolute;top:0;left:0;width:1200px;height:42px;background:rgba(0,0,0,.78);display:flex;justify-content:space-around;align-items:center;font-size:10px;color:#fff;font-weight:500}
.ticker b{background:var(--up);color:#fff;font-size:8px;padding:2px 4px;margin-left:5px;border-radius:2px}
.masthead{position:absolute;top:42px;left:0;width:1200px;height:88px;border-bottom:1px solid rgba(255,255,255,.15)}
.brand{position:absolute;left:130px;top:32px;display:flex;align-items:center;gap:10px;color:#e9e2d5;font-size:13px;font-weight:500;letter-spacing:1.5px;text-transform:uppercase}
.brand i{width:22px;height:22px;border-radius:50%;background:#d9cfbe;display:block}
.phone{position:absolute;left:615px;top:34px;color:#fff;font-size:13px;font-weight:600;display:flex;gap:8px;align-items:center}
.search{position:absolute;left:790px;top:30px;width:160px;height:26px;border-bottom:1px solid rgba(255,255,255,.4);color:#ccc;font-size:10px;line-height:26px;padding-left:15px}
.icons{position:absolute;left:966px;top:34px;display:flex;gap:22px}
.nav{position:absolute;top:140px;left:130px;width:940px;display:flex;justify-content:space-between;color:#fff;font-size:11px;font-weight:700;letter-spacing:.3px}
.hero h1{position:absolute;left:130px;top:250px;width:520px;color:#fff;font-size:47px;line-height:53px;font-weight:900;text-transform:uppercase}
.hero p{position:absolute;left:130px;top:428px;width:400px;color:#fff;font-size:13px;line-height:21px}
.hero .btn{position:absolute;left:130px;top:534px;height:36px;line-height:36px;padding:0 26px}
.dots{position:absolute;top:646px;left:560px;display:flex;gap:8px}
.dots i{width:8px;height:8px;border-radius:50%;background:#fff;display:block}
.dots i.on{background:var(--gold)}

/* about */
.about{top:716px;height:844px}
.about h2{position:absolute;left:130px;top:70px;font-size:34px;font-weight:900;color:var(--ink);text-transform:uppercase}
.about .lead{position:absolute;left:130px;top:126px;width:920px;font-size:13px;line-height:21px;color:#444}
.ph{position:absolute}
.about .img1{left:130px;top:256px;width:484px;height:232px;background:linear-gradient(120deg,#e3e3e3 0%,#9b9b9b 45%,#4a4a4a 100%)}
.about .img2{left:239px;top:492px;width:427px;height:241px;background:radial-gradient(ellipse 200px 160px at 210px 110px,#ffc44a 0%,#f07f17 35%,#7a3309 70%,#241208 100%);box-shadow:0 6px 18px rgba(0,0,0,.25)}
.play{position:absolute;left:188px;top:96px;width:48px;height:48px;border-radius:50%;background:#111;display:flex;align-items:center;justify-content:center}
.circ{position:absolute;left:100px;top:572px;width:100px;height:100px;border-radius:50%;border:1px dashed #bbb;background:repeating-linear-gradient(45deg,#ddd 0 1px,transparent 1px 6px)}
.dotgrid{position:absolute;left:500px;top:226px;width:150px;height:140px;background-image:radial-gradient(#c9c9c9 1.3px,transparent 1.4px);background-size:12px 12px}
.about .side{position:absolute;left:740px;top:277px;width:305px;font-size:13px;line-height:21px;color:#444}
.about .side p+p{margin-top:18px}
.about .btn{position:absolute;left:740px;top:639px}

/* value cards */
.values{top:1560px;height:620px}
.card{position:absolute;top:0;width:296px;height:513px;background:linear-gradient(180deg,#f7ecdc,#efdcc0)}
.card h3{height:38px;line-height:38px;background:linear-gradient(90deg,#c48a44,#d7a360);color:#fff;font-size:11px;font-weight:700;padding-left:24px;text-transform:uppercase}
.card .pic{height:257px}
.card p{padding:24px 24px 0;font-size:11px;line-height:17px;color:#555;height:136px}
.card .btn{margin-left:24px;height:30px;line-height:30px}

/* personal */
.personal{top:2180px;height:662px;background:#0d0a07;overflow:hidden}
.personal .bg{position:absolute;inset:0;background:radial-gradient(ellipse 520px 420px at 380px 120px,#a0500f 0%,#4a2208 45%,#0d0a07 80%)}
.personal .portrait{position:absolute;left:640px;top:0;width:560px;height:662px;background:linear-gradient(180deg,#2a2421 0%,#151211 55%,#0b0a09 100%)}
.personal h2{position:absolute;left:130px;top:102px;color:#fff;font-size:47px;line-height:53px;font-weight:900;text-transform:uppercase}
.personal .copy{position:absolute;left:130px;top:230px;width:410px;color:#fff;font-size:13px;line-height:21px}
.personal .copy p+p{margin-top:21px}
.personal .btn{position:absolute;left:130px;top:521px}

/* testimonials */
.testimonials{top:2842px;height:488px;background:var(--grey-bg)}
.testimonials h2{position:absolute;top:74px;width:1200px;text-align:center;font-size:30px;font-weight:900;color:var(--ink);text-transform:uppercase}
.tcard{position:absolute;top:152px;width:296px;height:231px;background:#fff;box-shadow:0 4px 14px rgba(0,0,0,.08);padding:30px 30px}
.tcard .who{display:flex;align-items:center;gap:12px}
.av{width:34px;height:34px;border-radius:50%;background:#d9a65f;color:#fff;font-weight:700;display:flex;align-items:center;justify-content:center;font-size:14px}
.who small{display:block;font-size:9px;color:#333;line-height:13px}
.stars{color:#e7a52c;font-size:10px;letter-spacing:1px}
.src{margin-left:auto;width:18px;height:18px;border-radius:50%;border:2px solid #999}
.tcard p{margin-top:20px;font-size:10px;line-height:15px;color:#555}
.arrow{position:absolute;top:274px;width:36px;height:36px;border-radius:50%;background:#fff;box-shadow:0 2px 8px rgba(0,0,0,.12);display:flex;align-items:center;justify-content:center}

/* trust */
.trust{top:3330px;height:345px}
.trust h2{position:absolute;top:72px;width:1200px;text-align:center;font-size:30px;font-weight:900;color:var(--ink);text-transform:uppercase}
.badges{position:absolute;top:168px;left:110px;width:980px;display:flex}
.badge{flex:1;text-align:center;border-right:1px solid #ddd;height:110px}
.badge:last-child{border-right:0}
.medal{width:64px;height:64px;border-radius:50%;background:#111;margin:0 auto 6px;border:4px solid var(--gold)}
.plate{width:110px;height:42px;background:#1d3b6b;border-radius:4px;margin:10px auto 12px}
.badge b{display:block;font-size:13px;color:#111}
.badge small{font-size:8px;color:#555}

/* registration */
.register{top:3675px;height:1041px;background:var(--gold-band)}
.register h2{position:absolute;top:64px;width:1200px;text-align:center;font-size:33px;font-weight:900;color:#1a1a1a;text-transform:uppercase}
.panel{position:absolute;left:147px;top:140px;width:906px;height:855px;background:var(--gold-panel)}
.panel .acc{position:absolute;left:35px;width:836px;font-size:13px;font-weight:600;color:#2a2a2a;display:flex;justify-content:space-between;align-items:center}
.panel .acc.line{border-bottom:1px solid rgba(0,0,0,.25);padding-bottom:20px}
.tog{width:13px;height:13px;border-radius:50%;background:#222;color:var(--gold-panel);font-size:11px;line-height:13px;text-align:center;font-weight:700}
.field{position:absolute;width:413px;height:42px;background:#fff;font-size:11px;color:#555;line-height:42px;padding-left:18px}
.submit{position:absolute;left:370px;top:744px;width:166px;height:42px;background:#121212;color:#fff;font-size:11px;font-weight:700;text-align:center;line-height:42px}

/* footer */
.site-footer{top:4716px;height:675px;background:#1b1b1b;color:#ddd}
.perk{position:absolute;top:33px;width:293px;height:113px;padding:22px 20px;color:#fff}
.perk h4{font-size:15px;font-weight:700}
.perk p{font-size:9px;margin-top:24px;line-height:13px}
.perk a{display:block;font-size:9px;color:#9ab7ff;margin-top:4px}
.perk svg{position:absolute;right:18px;top:20px}
.cols{position:absolute;top:184px;left:155px;display:flex}
.col{width:179px;font-size:8px;line-height:13px;color:#ddd}
.col h5{font-size:8px;font-weight:500;color:#999;margin-bottom:6px}
.hours{position:absolute;left:873px;top:180px;width:170px;height:42px;border:1px solid #777;border-radius:3px;padding:6px 8px;font-size:9px;line-height:13px;color:#fff}
.belief{position:absolute;left:873px;top:240px;width:170px;font-size:9px;line-height:12px;color:#ddd}
.news{position:absolute;top:432px;left:280px;width:280px;text-align:center;font-size:9px;line-height:12px;color:#ddd}
.email{position:absolute;top:436px;left:710px;width:172px;height:24px;background:#fff;font-size:8px;color:#999;line-height:24px;padding-left:8px}
.email-go{position:absolute;top:436px;left:889px;width:26px;height:24px;background:#2b4fae}
.contact-bar{position:absolute;top:485px;left:0;width:1200px;height:51px;background:#dedede;color:#222;font-size:12px;font-weight:600}
.contact-bar span{position:absolute;text-align:center}
.social{position:absolute;top:560px;left:150px;display:flex;gap:10px;align-items:center;font-size:9px;color:#ddd}
.social i{width:14px;height:14px;border-radius:50%;background:#ddd;display:block}
.rights{position:absolute;top:594px;left:150px;font-size:9px;color:#ccc}
.foot-brand{position:absolute;top:622px;left:150px;display:flex;align-items:center;gap:14px;color:#fff;font-size:22px;font-weight:500;letter-spacing:2px;text-transform:uppercase}
.foot-brand i{width:40px;height:40px;border-radius:50%;background:#e6e6e6;display:block}
</style>
</head>
<body>

<section class="hero">
  <div class="hero-photo" role="img" aria-label="Molten gold pouring from a furnace with sparks inside the refinery"></div>
  <div class="ticker">
    <span>Gold $2,926.60<b>+4.56</b></span>
    <span>Silver $33.25<b>+0.16</b></span>
    <span>Platinum $994.92<b>+10.22</b></span>
    <span>Palladium $996.72<b>+10.92</b></span>
    <span>Gold $2,926.60<b>+4.56</b></span>
    <span>Gold $2,926.60<b>+4.56</b></span>
  </div>
  <div class="masthead">
    <div class="brand"><i></i>Steadfast Precious Metals Refineries</div>
    <div class="phone"><svg width="14" height="14" viewBox="0 0 24 24"><path fill="#e2a84c" d="M6.6 10.8a15 15 0 0 0 6.6 6.6l2.2-2.2c.3-.3.7-.4 1-.2 1.1.4 2.3.6 3.6.6.6 0 1 .4 1 1V20c0 .6-.4 1-1 1A17 17 0 0 1 3 4c0-.6.4-1 1-1h3.5c.6 0 1 .4 1 1 0 1.3.2 2.5.6 3.6.1.3 0 .7-.2 1z"/></svg>(503) 555-0142</div>
    <div class="search">Search...</div>
    <div class="icons">
      <svg width="16" height="16" viewBox="0 0 24 24"><circle cx="10" cy="10" r="6.5" fill="none" stroke="#fff" stroke-width="2.5"/><path d="M15 15l6 6" stroke="#fff" stroke-width="2.5"/></svg>
      <svg width="16" height="16" viewBox="0 0 24 24"><circle cx="12" cy="7" r="5" fill="#fff"/><path d="M3 22c0-5 4-8 9-8s9 3 9 8z" fill="#fff"/></svg>
      <svg width="14" height="16" viewBox="0 0 24 28"><path d="M12 0a10 10 0 0 0-10 10c0 8 10 18 10 18s10-10 10-18A10 10 0 0 0 12 0zm0 14a4 4 0 1 1 0-8 4 4 0 0 1 0 8z" fill="#fff"/></svg>
    </div>
  </div>
  <nav class="nav"><span>GOLD</span><span>SILVER</span><span>SHOP ALL</span><span>DEALS</span><span>SELL TO US</span><span>WE BUY</span><span>IRA</span><span>JEWELRY</span></nav>
  <h1>Our Precious Metal Refinery Process</h1>
  <p>Most refineries are set up to work on precious metals behind closed doors. Here at Steadfast KLV we not only invite you to witness your lot being melted; we encourage you to watch every</p>
  <span class="btn">Learn More</span>
  <div class="dots"><i></i><i class="on"></i><i></i><i></i><i></i></div>
</section>

<section class="about">
  <h2>About Our Precious Metal Refinery</h2>
  <p class="lead">Most refineries are set up to work on precious metals behind closed doors. Here at Steadfast KLV we not only invite you to witness your lot being melted; we encourage you to watch every step of your metals being processed. We have a comfortable waiting area with bulletproof walls and windows for you to witness the melting as it is taking place.</p>
  <div class="dotgrid"></div>
  <div class="circ"></div>
  <div class="ph img1" role="img" aria-label="Refinery technician handling equipment beside the furnace"></div>
  <div class="ph img2" role="img" aria-label="Video thumbnail of molten metal being poured in the refinery">
    <span class="play"><svg width="16" height="16" viewBox="0 0 16 16"><path d="M4 2l10 6-10 6z" fill="#fff"/></svg></span>
  </div>
  <div class="side">
    <p>Our precious metal refinery is equipped with the latest technology and state of the art assaying equipment used to test each lot of your precious metals, ensuring your results are both accurate and precise.</p>
    <p>You will receive an analysis of your metals; certifying the results and giving you peace of mind. We take pride in our timeliness and efficiency. We know that time is money and your time is valuable; we will give you your one-day settlement in a matter of hours, with your choice of cash, check or wire transfer. Please call ahead and schedule a same-day appointment at our facility.</p>
  </div>
  <span class="btn">Learn More</span>
</section>

<section class="values">
  <article class="card" style="left:130px">
    <h3>Optimize Your Earnings</h3>
    <div class="pic" role="img" aria-label="Gold jewelry scrap in a melting crucible" style="background:radial-gradient(ellipse 90px 80px at 150px 150px,#d9421c 0%,#b8862e 40%,#2a2a2a 75%,#cfcfcf 100%)"></div>
    <p>You are able to receive the most cash for your silver through us. Why? Because we are the refinery! This allows us to give you the most money. No need to go through cash for gold places or pawn shops, our in-house refinery gives you direct access to</p>
    <span class="btn">Learn More</span>
  </article>
  <article class="card" style="left:452px">
    <h3>No Middle-Man</h3>
    <div class="pic" role="img" aria-label="Glowing crucible inside an induction furnace" style="background:radial-gradient(ellipse 70px 90px at 150px 140px,#ffb34a 0%,#e0741a 35%,#6a6a6a 70%,#d9d9d9 100%)"></div>
    <p>At Steadfast KLV we melt gold and silver received from buying gold and authorized dealers such as pawn shops and we buy gold places. Doesn’t it make sense to cut them out? Deal direct with us, we’re confident you’ll walk out happy!</p>
    <span class="btn">Learn More</span>
  </article>
  <article class="card" style="left:773px">
    <h3>Trust &amp; Reputation</h3>
    <div class="pic" role="img" aria-label="Molten gold poured into an ingot mold" style="background:radial-gradient(ellipse 70px 110px at 140px 150px,#ffd06a 0%,#f39a25 35%,#5a3a1a 70%,#3a3a3a 100%)"></div>
    <p>Dealing direct also gives you access to our resources, industry standard technology allowing us to treat your items with the utmost care. Our process is risk-free as we maintain the integrity of your jewelry through our non-invasive process whether or not</p>
    <span class="btn">Learn More</span>
  </article>
</section>

<section class="personal">
  <div class="bg" role="img" aria-label="Furnace glow in the background of the refinery floor"></div>
  <div class="portrait" role="img" aria-label="Portrait of a refinery team member in a black shirt"></div>
  <h2>Personal<br>Relationships</h2>
  <div class="copy">
    <p>We at Steadfast Precious Metals Refineries recognize the value of personal relationships and the details that take service from good to great. We strive to build a personal relationship with our clients. By gaining your confidence and giving consistent accurate results, we work diligently to earn your trust. Ensuring our client’s complete satisfaction is our number one goal.</p>
    <p>Steadfast Precious Metals Refineries is built on the idea that trust is the most important asset to a successful business. We strive to earn your trust and confidence every day through transparency, accuracy and personal relationships with each and every client.</p>
  </div>
  <span class="btn">Learn More</span>
</section>

<section class="testimonials">
  <h2>Testimonials</h2>
  <span class="arrow" style="left:62px"><svg width="14" height="14" viewBox="0 0 14 14"><path d="M13 7H2M6 2L1 7l5 5" stroke="#222" stroke-width="1.6" fill="none"/></svg></span>
  <span class="arrow" style="left:1094px"><svg width="14" height="14" viewBox="0 0 14 14"><path d="M1 7h11M8 2l5 5-5 5" stroke="#222" stroke-width="1.6" fill="none"/></svg></span>
  <div class="tcard" style="left:130px">
    <div class="who"><span class="av">L</span><div><small>Lena Marsh</small><small>Rating: 5 · 41 reviews</small><span class="stars">★★★★★</span></div><span class="src"></span></div>
    <p>Steadfast Precious Metals Coins, Jewelry &amp; Diamonds is an outstanding place for anyone looking to buy or sell precious metals. Their customer service is top-notch if they don’t have what you’re looking for, they’ll go the extra mile to get it in stock and notify you when it arrives. Selling to them</p>
  </div>
  <div class="tcard" style="left:452px">
    <div class="who"><span class="av">L</span><div><small>Lena Marsh</small><small>Rating: 5 · 41 reviews</small><span class="stars">★★★★★</span></div><span class="src"></span></div>
    <p>Steadfast Precious Metals Coins, Jewelry &amp; Diamonds is an outstanding place for anyone looking to buy or sell precious metals. Their customer service is top-notch if they don’t have what you’re looking for, they’ll go the extra mile to get it in stock and notify you when it arrives. Selling to them</p>
  </div>
  <div class="tcard" style="left:773px">
    <div class="who"><span class="av">L</span><div><small>Lena Marsh</small><small>Rating: 5 · 41 reviews</small><span class="stars">★★★★★</span></div><span class="src"></span></div>
    <p>Steadfast Precious Metals Coins, Jewelry &amp; Diamonds is an outstanding place for anyone looking to buy or sell precious metals. Their customer service is top-notch if they don’t have what you’re looking for, they’ll go the extra mile to get it in stock and notify you when it arrives. Selling to them</p>
  </div>
</section>

<section class="trust">
  <h2>Your Most Trusted Gold Buyer</h2>
  <div class="badges">
    <div class="badge"><div class="medal"></div><b>12+ years</b><small>in business</small></div>
    <div class="badge"><div class="medal"></div><b>4.8/5 stars</b><small>1,000+ online reviews</small></div>
    <div class="badge"><div class="medal"></div><b>100,000+</b><small>satisfied customers</small></div>
    <div class="badge"><div class="medal"></div><b>$250,000,000+</b><small>bought &amp; sold</small></div>
    <div class="badge"><div class="plate"></div><small style="font-size:9px;font-weight:600;color:#111">Click for Profile</small></div>
  </div>
</section>

<section class="register">
  <h2>Wholesale Registration</h2>
  <form class="panel">
    <div class="acc" style="top:38px">Business Contact Information<span class="tog">–</span></div>
    <div class="field" style="left:35px;top:86px">Legal Business Name</div>
    <div class="field" style="left:458px;top:86px">City</div>
    <div class="field" style="left:35px;top:138px">Company Phone</div>
    <div class="field" style="left:458px;top:138px">State</div>
    <div class="field" style="left:35px;top:190px">Email</div>
    <div class="field" style="left:458px;top:190px">Zip</div>
    <div class="field" style="left:35px;top:245px">Company Physical Address</div>
    <div class="field" style="left:458px;top:245px">Federal ID/EIN#</div>
    <div class="field" style="left:35px;top:298px">Date Business Commenced</div>
    <div class="field" style="left:458px;top:298px">Business Type</div>
    <div class="field" style="left:35px;top:350px">Website</div>
    <div class="acc line" style="top:410px">Primary Owner or Principal<span class="tog">+</span></div>
    <div class="acc line" style="top:480px">Secondary Owner or Principal<span class="tog">+</span></div>
    <div class="acc line" style="top:545px">Billing<span class="tog">+</span></div>
    <div class="acc line" style="top:604px">Shipping<span class="tog">+</span></div>
    <div class="acc" style="top:669px">Terms and Conditions<span class="tog">+</span></div>
    <div class="submit">SUBMIT</div>
  </form>
</section>

<footer class="site-footer">
  <div class="perk" style="left:147px;background:#2c2c2c">
    <h4>Price match guarantee</h4>
    <svg width="18" height="18" viewBox="0 0 24 24"><circle cx="12" cy="12" r="10" fill="none" stroke="#ccc" stroke-width="1.6"/><path d="M7 12l3 3 7-7" stroke="#ccc" stroke-width="1.6" fill="none"/></svg>
    <p>on all bullion products.</p><a>Learn more</a>
  </div>
  <div class="perk" style="left:450px;background:#1d2a5a">
    <h4>100% Insured</h4>
    <svg width="18" height="18" viewBox="0 0 24 24"><path d="M12 2l8 3v7c0 5-4 9-8 10-4-1-8-5-8-10V5z" fill="none" stroke="#ccc" stroke-width="1.6"/><path d="M8 12l3 3 5-5" stroke="#ccc" stroke-width="1.6" fill="none"/></svg>
    <p style="margin-top:36px">All orders are tracked and insured.</p>
  </div>
  <div class="perk" style="left:754px;background:linear-gradient(90deg,#3b3a1e,#7a6a2a)">
    <h4>Free Shipping</h4>
    <svg width="22" height="18" viewBox="0 0 28 20"><path d="M1 3h16v11H1zM17 7h6l4 4v3h-10z" fill="none" stroke="#ccc" stroke-width="1.6"/><circle cx="7" cy="16" r="2" fill="#ccc"/><circle cx="21" cy="16" r="2" fill="#ccc"/></svg>
    <p style="margin-top:14px">Orders ship free over $499.<br><small style="font-size:6px">Terms apply</small></p><a>Shop now</a>
  </div>

  <div class="cols">
    <div class="col"><h5>Buying &amp; selling</h5>Shop Bullion<br>IRA Bullion<br>Silver Bullion<br>Gold Bullion<br>Platinum Bullion<br>Palladium Bullion<br>Steadfast Jewelry</div>
    <div class="col"><h5>Company</h5>Leave a Review<br>Testimonials<br>Refinery Process<br>Blog<br>About Us</div>
    <div class="col"><h5>Customer care</h5>My account<br>Investment Tools<br>Contact us<br>FAQs<br>Jewelry 101<br>Jewelry Repair</div>
    <div class="col"><h5>Legal</h5>Privacy Policy<br>Terms and Conditions<br>Mail-In Terms<br>Acceptable Use<br>Cookie Policy<br>Disclaimer Policy<br>Payment Terms<br>Shipping Policy<br>Returns Policy<br>Price Match<br>Affiliate Program Terms of Use</div>
  </div>
  <div class="hours">Open Mon–Fri<br>10:00a – 6:00p PST</div>
  <div class="belief">Steadfast Precious Metals Refineries is a proudly patriotic Christian business in the United States of America.
    <div style="display:flex;gap:20px;margin-top:8px;align-items:center">
      <svg width="14" height="22" viewBox="0 0 14 22"><path d="M7 0v22M1 6h12" stroke="#fff" stroke-width="2.5"/></svg>
      <svg width="40" height="22" viewBox="0 0 40 22"><rect width="40" height="22" fill="#fff"/><g fill="#c0282d"><rect y="0" width="40" height="3"/><rect y="6" width="40" height="3"/><rect y="12" width="40" height="3"/><rect y="18" width="40" height="3"/></g><rect width="17" height="12" fill="#2a3a80"/></svg>
    </div>
  </div>

  <div class="news">Subscribe to our newsletter to be the first to know about special deals and promotions.</div>
  <div class="email">Enter Email</div>
  <div class="email-go"></div>

  <div class="contact-bar">
    <span style="left:210px;width:170px;top:18px">(503) 555-0142</span>
    <span style="left:480px;width:240px;top:11px;font-size:11px;line-height:14px">2210 Larkspur Ave NE,<br>Brennick, ND 58000</span>
    <span style="left:800px;width:210px;top:18px">info@steadfastklv.com</span>
  </div>
  <div class="social">Follow us on social media to stay up to date: <i></i><i></i><i></i><i></i><i></i></div>
  <div class="rights">© 2025 All Rights Reserved Steadfast Precious Metals Refineries</div>
  <div class="foot-brand"><i></i>Steadfast Precious Metals Refineries</div>
</footer>

</body>
</html>
```